Upgrade website from just a link tree to a full adult content site with payment gateway.

I would like to upgrade my website VelvetKestrel.com and turn it into a pay site with a payment gateway to my content. I would like to use Wordpress. The designer needs to produce a front page with membership sign up link, payment gateway which would then provide access to the content page. We would need to be able to then go in and edit (if necessary) and load all of the content. We would like this to be as easy as possible and already have paid for a Wordpress license. We could simply allow access to our hostnimbo/Wordpress account so you can build it once all the details are confirmed. Needs to be simple to upload and have a format all set to go where we would just log in and do it. May need directions or a tutorial to get us started on the path. We are open to suggestions and ideas. We will be providing adult content. Four pages I believe. Front page , gateway video content page and picture content page. The video and picture content goes really just need to be a layout and then we can drop the videos and images in there. You can ask any other relevant questions and we can update the brief. Sorry we are fairly new to this so this is why we are looking to professionals to lead the way. Please look at current webpage for an idea of how we like the current format. It can be replicated or it can be changed. We will market and funnel our online and SoCial accounts to this page on hopes people sign up and pay membership for access to the content past the first page. Check VelvetKestrel.com for an idea of how we want to move forward. Someone goes to page. We would like to see: They can click on member log in if they have already signed up or click join and go to the payment gateway page where they can choose their membership. Once they are paid they produce their log in and lassoed. Sign in and have access to the content pages. One page can be for photos and one page can be for videos. Would consider a live stream if possible but not mandatory. Basically we want to provide content people can view for a fee. A water mark would also be nice to protect our images and video. Also if there is a way to not allow the content to be downloaded. But a water mark would protect that.

Target Market(s)

Adult entertainment

Industry/Entity Type

Adult entertainment

Coding

Coded - Design and coding required

Number of Pages Required

4 page

Font styles to use
Decorative
Script

Colors
E54698
E96AAD
F1A4CE
F9D9EA
FCEFF6
A7469A
B969AE
D3A5CF
EDDBEB
F8F0F9

Requirements
Must have
• Front page. Gateway Payment/membership sign up. Video content page set up and image content page set up. Water mark we can put on content.
Nice to have
• Live video feed capabilities. Watermark.
Should not have
• Free access to the content.

```html
<!DOCTYPE html>
<html lang="en">
<head>
<meta charset="utf-8">
<title>VelvetKestrel – Signup</title>
<link rel="stylesheet" href="https://fonts.googleapis.com/css2?family=Great+Vibes&family=Montserrat:wght@400;500;600&display=swap">
<style>
  :root {
    --pink: #F1A4CE;
    --pink-strong: #E96AAD;
    --pink-button: #EBA6CC;
    --white: #FFFFFF;
    --black: #000000;
  }
  * { box-sizing: border-box; margin: 0; padding: 0; }
  html, body { width: 1200px; height: 890px; overflow: hidden; background: var(--black); }
  body { position: relative; font-family: "Montserrat", sans-serif; color: var(--white); }

  .hero-backdrop {
    position: absolute; left: 0; top: 0; width: 1200px; height: 798px;
    background:
      radial-gradient(ellipse 420px 260px at 560px 230px, #3a3a3a 0%, rgba(40,40,40,0) 70%),
      radial-gradient(ellipse 500px 300px at 1050px 150px, #4a4a4a 0%, rgba(50,50,50,0) 70%),
      linear-gradient(160deg, #2e2e2e 0%, #1b1b1b 45%, #101010 70%, #262626 100%);
  }

  .brand {
    position: absolute; left: 58px; top: 62px;
    font-size: 30px; font-weight: 500; letter-spacing: 0.5px; color: var(--white);
  }

  .contact {
    position: absolute; left: 912px; top: 25px;
    display: flex; align-items: center; gap: 10px; font-size: 12.5px;
  }

  .main-nav { position: absolute; top: 57px; left: 0; width: 1200px; height: 26px; }
  .main-nav a {
    position: absolute; top: 2px; color: var(--white); text-decoration: none; font-size: 17px;
  }
  .main-nav .login {
    top: 0; left: 1044px; width: 57px; height: 25px; line-height: 25px; text-align: center;
    background: var(--pink-button); border-radius: 2px; font-size: 13px;
  }

  .page-title {
    position: absolute; left: 0; width: 1200px; top: 148px; text-align: center;
    font-family: "Great Vibes", cursive; font-size: 74px; color: var(--pink); font-weight: 400;
  }
  .section-title {
    position: absolute; left: 0; width: 1200px; top: 297px; text-align: center;
    font-size: 19px; color: var(--pink); font-weight: 400;
  }

  .field {
    position: absolute; left: 236px; width: 290px; height: 44px;
    border: 1px solid var(--pink);
  }
  .field legend, .summary legend {
    margin-left: 40px; font-size: 8.5px; color: var(--pink); line-height: 8px;
  }
  .field legend { padding: 0 24px; }
  .field.cvv { width: 152px; }
  .field.cvv legend { margin-left: 21px; padding: 0 17px; }

  .card-name {
    position: absolute; top: 566px; font-size: 10.5px; font-weight: 600; color: var(--pink);
  }

  .submit {
    position: absolute; left: 237px; top: 630px; width: 289px; height: 40px;
    border: none; border-radius: 20px; background: var(--pink-button);
    color: var(--white); font-family: "Montserrat", sans-serif; font-size: 13px; letter-spacing: 0.2px;
  }

  .summary {
    position: absolute; left: 680px; top: 360px; width: 289px; height: 233px;
    border: 1px solid var(--pink);
  }
  .summary legend { padding: 0 16px; }
  .summary-row { position: absolute; left: 18px; font-size: 13px; color: var(--pink); }
  .summary-row .value { position: absolute; left: 130px; white-space: nowrap; font-weight: 500; }

  .site-footer {
    position: absolute; left: 0; top: 798px; width: 1200px; height: 92px;
    background: var(--black); border-top: 1px solid #bdbdbd;
    text-align: center; font-size: 15.5px; line-height: 88px;
  }
  .site-footer strong { font-weight: 600; }
</style>
</head>
<body>
  <div class="hero-backdrop" role="img" aria-label="Dark monochrome boudoir photograph filling the page background"></div>

  <div class="brand">VelvetKestrel</div>

  <div class="contact">
    <svg width="18" height="14" viewBox="0 0 18 14" aria-hidden="true">
      <rect x="0.5" y="0.5" width="17" height="13" fill="none" stroke="#fff" stroke-width="1"/>
      <path d="M0.5 0.5 L9 8 L17.5 0.5 M0.5 13.5 L7 6.5 M17.5 13.5 L11 6.5" fill="none" stroke="#fff" stroke-width="1"/>
    </svg>
    <span>velvetkestrel@mailnest.com</span>
  </div>

  <nav class="main-nav">
    <a href="#" style="left:590px">Home</a>
    <a href="#" style="left:688px">Membership</a>
    <a href="#" style="left:838px">Videos</a>
    <a href="#" style="left:941px">Gallery</a>
    <a href="#" class="login">Login</a>
  </nav>

  <h1 class="page-title">Signup</h1>
  <h2 class="section-title">CHECK OUT PAGE:</h2>

  <fieldset class="field" style="top:360px"><legend>First Name</legend></fieldset>
  <fieldset class="field" style="top:424px"><legend>Last Name</legend></fieldset>
  <fieldset class="field" style="top:488px"><legend>Card Number</legend></fieldset>
  <fieldset class="field cvv" style="top:552px"><legend>CVV</legend></fieldset>

  <span class="card-name" style="left:406px">PayOrbit</span>
  <span class="card-name" style="left:464px">CardSphere</span>

  <button class="submit">SUBMIT PAYMENT</button>

  <fieldset class="summary">
    <legend>TOTAL AMOUNT</legend>
    <div class="summary-row" style="top:33px">MEMBERSHIP:<span class="value">MONTHLY</span></div>
    <div class="summary-row" style="top:80px">AMOUNT:<span class="value">$199.00</span></div>
    <div class="summary-row" style="top:127px">DISCOUNT:<span class="value">$0.00</span></div>
    <div class="summary-row" style="top:174px">TOTAL:<span class="value">$199.00</span></div>
  </fieldset>

  <footer class="site-footer">
    Copyright © 2020-2021 VelvetKestrel | <strong>Privacy</strong> | <strong>Terms</strong>
  </footer>
</body>
</html>
```